Home Page Design for Motor Manufacturer

Hello,
please design the homepage for a manufacturer of industry motors. I am looking for a professional, clean and minimalistic design. Since this a rather conservative industry it should get a professional look but since it is a redesign there should be some modern that gives is the modern touch of innovation.
A competitor's homepage I like is:
https://www.valdorix.example/en/
What I like about this website:
* clean, minimal, well structured design
* mega menu
For this project please find attached the wireframes (most buttons are in German but by context and Google translate you will easily figure it out; only unclear - "Messe" means "trade exhibition"). The paddings and margins are NOT exact. Also any color of backgrounds etc. chosen is not meant to represent a real color but rather to illustrate the object and maybe show there should be some background emphasis (color or image).
Wireframes:
https: //www.filnest. example / t / pQmW7zKtRb3LyaHx
In both wireframes the only thing that is different is the Service section. I expect from the winner both designs for this service section: one with normal cart design and one with tabs as filters to search products (find image for product categories attached)
In the header use on the left the following text:
h1: "Your competent partner for industrial engines,
-transmission and drawing parts
with more than 5000 satisfied customers "
primary button: Our products
sec. button: Download catalog
and on the right side we feature one or more product images (like putting them in a nice display together).
I also think of a solid background color or subtle gradient for the hero section.
The winner should also design an open mega menu version.
Menu items in this order:
• Home page
• Gearboxes & Motors
• Engine components
• Drawing parts
• Machines & accessories
• About us
• Contact
Also create a language switch with globe symbol and DE for Germany and EN for English above the nav plus the telephone number with icon (user dummy number +49 (0) 987654321)
Output should be in Figma, Sketch or PSD.
Fonts + color to use:
header: Proza Libre, bold, # 0171A1
body: Open Sans, regular, black
Primary accent color: # 0171A1
Text black or dark gray
background: light gray, white or shade of blue
More image resources:
https://www.filnest.example/t/ZuTn4VcqMh8ErwJo
If there are any questions please do not hesitate to ask.
Target Market(s)
B2B - anyone with industrial machinery needing small motors (not car engines)
Industry/Entity Type
Manufacturing
Number of Pages Required
1 page
Requirements
Must have
- see above
Nice to have
- see above
Should not have
- see above

```html
<!DOCTYPE html>
<html lang="en">
<head>
<meta charset="utf-8">
<title>KVM – Industrial Motors</title>
<link href="https://fonts.googleapis.com/css2?family=Open+Sans:wght@400;600;700&family=Proza+Libre:wght@400;600;700&display=swap" rel="stylesheet">
<style>
:root{
  --blue:#0171A1;
  --blue-dark:#015a80;
  --black:#111;
  --text:#333;
  --muted:#777;
  --light:#f3f3f3;
  --line:#e2e2e2;
  --teal:#aad6df;
  --footer:#2f2f2f;
}
*{box-sizing:border-box;margin:0;padding:0}
html,body{width:1200px;height:4498px;overflow:hidden}
body{font-family:"Open Sans",sans-serif;color:var(--text);background:#fff;position:relative}
.abs{position:absolute}
h1,h2,h3,h4,.head{font-family:"Proza Libre",sans-serif;color:var(--black)}
a{color:inherit;text-decoration:none}

/* top bar */
.brand{left:161px;top:10px;font-family:"Proza Libre",sans-serif;font-weight:700;font-size:36px;color:var(--blue);display:flex;align-items:center;gap:8px}
.brand i{display:block;width:14px;height:14px;background:var(--blue);border-radius:50%}
.search{left:316px;top:12px;width:386px;height:37px;border:1px solid var(--line);border-radius:19px;display:flex;overflow:hidden}
.search .tag{background:var(--blue);color:#fff;font-size:11px;font-weight:600;padding:0 18px;display:flex;align-items:center}
.search .field{flex:1;font-size:11px;color:var(--muted);display:flex;align-items:center;padding-left:16px}
.search .go{width:36px;border-left:1px solid var(--line);display:flex;align-items:center;justify-content:center}
.call{left:762px;top:16px;display:flex;gap:8px;align-items:center}
.call small{display:block;font-size:8px;color:var(--muted)}
.call b{display:block;font-size:12px;color:var(--blue)}
.lang{left:914px;top:22px;font-size:11px;color:var(--muted);display:flex;gap:6px;align-items:center}

/* nav */
.nav{left:0;top:60px;width:1200px;height:48px;background:var(--blue)}
.nav span{position:absolute;top:0;height:48px;line-height:48px;font-size:11px;font-weight:700;color:#fff}
.nav span.active{background:#fff;color:var(--blue);padding:0 10px}

/* hero */
.hero{left:0;top:108px;width:1200px;height:524px;background:linear-gradient(160deg,#3a3a38 0%,#1e1d1b 45%,#4a3f33 70%,#2a2622 100%)}
.arrow{width:42px;height:42px;border-radius:50%;background:rgba(0,0,0,.55);display:flex;align-items:center;justify-content:center}
.hero-card{left:318px;top:250px;width:559px;height:240px;display:flex}
.hero-card .main{width:376px;background:#fff;padding:30px 26px}
.hero-card .main h1{font-size:18px;line-height:1.4;font-weight:700}
.hero-card .main p{font-size:13px;color:var(--black);margin-top:8px}
.btns{display:flex;gap:14px;margin-top:14px}
.btn{font-size:11px;padding:8px 22px;display:inline-block}
.btn-blue{background:var(--blue);color:#fff}
.btn-ghost{border:1px solid var(--blue);color:var(--text)}
.btn-black{background:#000;color:#fff;font-weight:700;font-size:10px;text-transform:uppercase}
.hero-card .side{flex:1;background:#f0f0f0;padding:30px 16px;font-size:11px;color:var(--muted)}
.mega{left:206px;top:108px;width:663px;height:268px;background:#fff;box-shadow:0 4px 14px rgba(0,0,0,.15);display:flex;padding:22px 24px}
.mega .col{flex:1}
.mega h4{font-family:"Open Sans",sans-serif;font-size:12px;font-weight:600;margin-bottom:18px}
.mega li{list-style:none;font-size:10px;color:#999;height:24px}
.mega li::before{content:"";display:inline-block;width:4px;height:4px;border-radius:50%;background:#bbb;margin-right:6px;vertical-align:middle}

/* features */
.features{left:192px;top:559px;width:800px;height:259px;display:flex;gap:2px}
.feature{flex:1;background:#fff;box-shadow:0 2px 8px rgba(0,0,0,.1);text-align:center;padding-top:30px}
.feature h3{font-size:17px;margin-top:10px}
.feature hr{width:40px;border:0;border-top:2px solid var(--blue);margin:10px auto}
.feature p{font-size:11px;color:var(--muted);line-height:1.3;padding:0 22px}
.circ{width:30px;height:30px;border-radius:50%;background:var(--blue);margin:18px auto 0;display:flex;align-items:center;justify-content:center}

/* sections */
.bg-light{left:0;width:1200px;background:var(--light)}
.sec-title{width:1200px;left:0;text-align:center;font-size:26px;font-weight:400}
.product{width:423px;height:176px;background:#fff;display:flex;align-items:center;padding:0 18px}
.pic{border-radius:50%;background:radial-gradient(circle at 60% 45%,#5cc4e0 0,#2a6f86 30%,#3a3a3a 55%,#c9c9c9 75%,#f4f4f4 90%)}
.product .pic{width:105px;height:84px;flex:none}
.product .info{margin-left:22px}
.product h3{font-size:14px;font-weight:400}
.product p{font-size:10px;color:var(--text);line-height:1.9;margin:8px 0 10px}
.measure{left:162px;width:869px;border:1px solid var(--line);background:#fff;box-shadow:0 1px 4px rgba(0,0,0,.05)}
.measure .ring{left:43px;top:40px;width:190px;height:190px;border-radius:50%;border:2px solid #eee;background:radial-gradient(circle at 50% 55%,#555 0,#777 28%,#d8d8d8 48%,#fff 70%)}
.measure h3{left:262px;top:50px;font-size:17px;font-weight:400}
.measure p{left:262px;top:84px;width:560px;font-size:10px;line-height:1.9;color:var(--text)}
.measure .acts{right:54px;top:206px;display:flex;gap:12px}
.measure .btn{font-size:10px;font-weight:700;padding:9px 22px}

/* about */
.about-title{left:162px;top:2856px;font-size:27px;font-weight:700}
.about-bar{left:162px;top:2910px;width:60px;height:253px;background:var(--blue)}
.about-text{left:248px;top:2910px;width:330px}
.about-text .lead{font-size:12px;font-weight:600;color:var(--black);line-height:1.8}
.about-text p{font-size:10px;line-height:1.8;color:var(--muted);margin-top:14px}
.photo-big{left:672px;top:2852px;width:366px;height:366px;border-radius:50%;border:5px solid var(--blue);background:linear-gradient(135deg,#8a6e55 0%,#c9b59c 45%,#e9e1d6 70%,#9c8a78 100%)}
.photo-small{left:594px;top:2997px;width:222px;height:222px;border-radius:50%;border:4px solid var(--blue);background:radial-gradient(circle at 50% 50%,#222 0,#3a3a3a 35%,#e8e8e8 60%,#fff 100%)}

/* downloads */
.dl-photo{left:0;top:3280px;width:601px;height:498px;background:linear-gradient(140deg,#111 0%,#3c3c3c 35%,#6d6d6d 55%,#2a2a2a 80%,#0e0e0e 100%)}
.dl-text{left:662px;top:3352px;width:380px}
.dl-text h2{font-size:27px;font-weight:700}
.dl-text p{font-size:10px;line-height:1.8;color:var(--muted);margin-top:14px}
.dl-btn{left:667px;top:3672px;width:135px;height:36px;border:1px solid var(--blue);font-size:10px;display:flex;align-items:center;justify-content:center;gap:4px;color:var(--black)}

/* contact */
.contact{left:0;top:3778px;width:1200px;height:271px;background:linear-gradient(90deg,#a4d3dc,#bfe2e8,#a4d3dc)}
.contact h2{position:absolute;left:0;width:1200px;top:74px;text-align:center;font-size:27px;font-weight:700}
.input{height:36px;background:#fff;border:1px solid #ddd;font-size:10px;color:var(--muted);padding-left:18px;display:flex;align-items:center}
.submit{left:536px;top:189px;width:128px;height:35px;background:var(--blue);color:#fff;font-size:11px;display:flex;align-items:center;justify-content:center}

/* info row */
.info-item{top:4080px;display:flex;gap:12px}
.info-item b{display:block;font-size:13px;font-weight:600;color:var(--black)}
.info-item span{display:block;font-size:10px;color:var(--muted);line-height:1.5}
.touch{left:917px;top:4101px;width:121px;height:32px;background:var(--blue);color:#fff;font-size:11px;display:flex;align-items:center;justify-content:center}
.divider{left:162px;top:4178px;width:876px;border-top:1px solid var(--line)}

/* footer */
.f-col h5{font-size:12px;font-weight:600;color:var(--black);margin-bottom:14px;text-transform:uppercase}
.f-col li{list-style:none;font-size:10px;color:var(--muted);height:24px}
.news-input{left:690px;top:4320px;width:248px;height:36px;border:1px solid var(--line);font-size:10px;color:var(--muted);padding-left:18px;display:flex;align-items:center}
.news-btn{left:938px;top:4320px;width:100px;height:36px;background:var(--blue);color:#fff;font-size:11px;display:flex;align-items:center;justify-content:center}
.socials{left:690px;top:4368px;display:flex;gap:6px}
.socials i{display:block;width:28px;height:28px;border-radius:50%;background:var(--blue)}
.bottom{left:0;top:4447px;width:1200px;height:51px;background:var(--footer);color:#ddd;font-size:10px}
</style>
</head>
<body>

<!-- top bar -->
<div class="abs brand"><i></i>KVM</div>
<div class="abs search">
  <div class="tag">Search Item</div>
  <div class="field">Search</div>
  <div class="go"><svg width="12" height="12" viewBox="0 0 12 12"><circle cx="5" cy="5" r="3.5" fill="none" stroke="#888" stroke-width="1.4"/><line x1="7.6" y1="7.6" x2="11" y2="11" stroke="#888" stroke-width="1.4"/></svg></div>
</div>
<div class="abs call">
  <svg width="16" height="16" viewBox="0 0 24 24"><path d="M6.6 10.8a15 15 0 0 0 6.6 6.6l2.2-2.2c.3-.3.7-.4 1-.2 1.1.4 2.3.6 3.6.6.6 0 1 .4 1 1V20c0 .6-.4 1-1 1A17 17 0 0 1 3 4c0-.6.4-1 1-1h3.5c.6 0 1 .4 1 1 0 1.3.2 2.5.6 3.6.1.3 0 .7-.2 1z" fill="#0171A1"/></svg>
  <div><small>Call for Any Question</small><b>+49 (0) 987654321</b></div>
</div>
<div class="abs lang">
  <svg width="14" height="14" viewBox="0 0 14 14"><circle cx="7" cy="7" r="6" fill="#0171A1"/><ellipse cx="7" cy="7" rx="2.5" ry="6" fill="none" stroke="#fff" stroke-width=".9"/><line x1="1" y1="7" x2="13" y2="7" stroke="#fff" stroke-width=".9"/></svg>
  Select Language
  <svg width="8" height="6" viewBox="0 0 8 6"><path d="M1 1l3 3 3-3" fill="none" stroke="#777" stroke-width="1.4"/></svg>
</div>

<!-- nav -->
<nav class="abs nav">
  <span style="left:161px">Home</span>
  <span class="active" style="left:206px">Gearboxes &amp; Motors ⌄</span>
  <span style="left:364px">Engine Components ⌄</span>
  <span style="left:510px">Drawing Parts ⌄</span>
  <span style="left:625px">Machines &amp; Accessories ⌄</span>
  <span style="left:788px">About Us</span>
  <span style="left:863px">Contact</span>
  <svg class="abs" style="left:1014px;top:14px" width="18" height="20" viewBox="0 0 18 20"><circle cx="9" cy="6" r="4.5" fill="none" stroke="#fff" stroke-width="1.5"/><path d="M1 19c0-4.5 3.6-7 8-7s8 2.5 8 7" fill="none" stroke="#fff" stroke-width="1.5"/></svg>
</nav>

<!-- hero -->
<div class="abs hero" role="img" aria-label="Dark photo of an industrial factory hall"></div>
<div class="abs arrow" style="left:8px;top:350px"><svg width="12" height="14" viewBox="0 0 12 14"><path d="M8 2L3 7l5 5" fill="none" stroke="#fff" stroke-width="2.4"/></svg></div>
<div class="abs arrow" style="left:1130px;top:350px"><svg width="12" height="14" viewBox="0 0 12 14"><path d="M4 2l5 5-5 5" fill="none" stroke="#fff" stroke-width="2.4"/></svg></div>

<div class="abs hero-card">
  <div class="main">
    <h1>Your competent partner for industrial engines, transmission and drawing parts</h1>
    <p>with more than 5000 satisfied customers</p>
    <div class="btns"><span class="btn btn-blue">Our Products</span><span class="btn btn-ghost">Download Catalog</span></div>
  </div>
  <div class="side">
    Lorem ipsum dolor sit amet, consectetur adipiscing elit.
    <div style="margin-top:14px"><span class="btn btn-blue" style="padding:8px 16px">View More</span></div>
  </div>
</div>

<div class="abs mega">
  <div class="col"><h4>Menu List 01</h4><ul><li>Category Item 01</li><li>Category Item 01</li><li>Category Item 01</li><li>Category Item 01</li><li>Category Item 01</li><li>Category Item 01</li><li>Category Item 01</li><li>Category Item 01</li></ul></div>
  <div class="col"><h4>Menu List 01</h4><ul><li>Category Item 01</li><li>Category Item 01</li><li>Category Item 01</li><li>Category Item 01</li><li>Category Item 01</li><li>Category Item 01</li><li>Category Item 01</li><li>Category Item 01</li></ul></div>
  <div class="col"><h4>Menu List 01</h4><ul><li>Category Item 01</li><li>Category Item 01</li><li>Category Item 01</li><li>Category Item 01</li><li>Category Item 01</li><li>Category Item 01</li><li>Category Item 01</li><li>Category Item 01</li></ul></div>
  <div class="col"><h4>Menu List 01</h4><ul><li>Category Item 01</li><li>Category Item 01</li><li>Category Item 01</li><li>Category Item 01</li><li>Category Item 01</li><li>Category Item 01</li><li>Category Item 01</li><li>Category Item 01</li></ul></div>
</div>

<!-- features -->
<div class="abs features">
  <div class="feature">
    <svg width="38" height="34" viewBox="0 0 38 34"><path d="M3 32V12l8-5v5l8-5v5l8-5V2h6v30z" fill="none" stroke="#0171A1" stroke-width="2"/><rect x="8" y="18" width="5" height="5" fill="#5fb3d6"/><rect x="16" y="18" width="5" height="5" fill="#5fb3d6"/><rect x="24" y="18" width="5" height="5" fill="#5fb3d6"/><line x1="1" y1="32" x2="37" y2="32" stroke="#0171A1" stroke-width="2"/></svg>
    <h3>Feature 01</h3><hr><p>Lorem ipsum dolor sit amet, consectetur adipiscing elit. Donec faucibus consequat dui sit amet consequat.</p>
    <div class="circ"><svg width="8" height="10" viewBox="0 0 8 10"><path d="M2 1l4 4-4 4" fill="none" stroke="#fff" stroke-width="2"/></svg></div>
  </div>
  <div class="feature">
    <svg width="38" height="34" viewBox="0 0 38 34"><path d="M3 32V12l8-5v5l8-5v5l8-5V2h6v30z" fill="none" stroke="#0171A1" stroke-width="2"/><rect x="8" y="18" width="5" height="5" fill="#5fb3d6"/><rect x="16" y="18" width="5" height="5" fill="#5fb3d6"/><rect x="24" y="18" width="5" height="5" fill="#5fb3d6"/><line x1="1" y1="32" x2="37" y2="32" stroke="#0171A1" stroke-width="2"/></svg>
    <h3>Feature 02</h3><hr><p>Lorem ipsum dolor sit amet, consectetur adipiscing elit. Donec faucibus consequat dui sit amet consequat.</p>
    <div class="circ"><svg width="8" height="10" viewBox="0 0 8 10"><path d="M2 1l4 4-4 4" fill="none" stroke="#fff" stroke-width="2"/></svg></div>
  </div>
  <div class="feature">
    <svg width="38" height="34" viewBox="0 0 38 34"><path d="M3 32V12l8-5v5l8-5v5l8-5V2h6v30z" fill="none" stroke="#0171A1" stroke-width="2"/><rect x="8" y="18" width="5" height="5" fill="#5fb3d6"/><rect x="16" y="18" width="5" height="5" fill="#5fb3d6"/><rect x="24" y="18" width="5" height="5" fill="#5fb3d6"/><line x1="1" y1="32" x2="37" y2="32" stroke="#0171A1" stroke-width="2"/></svg>
    <h3>Feature 03</h3><hr><p>Lorem ipsum dolor sit amet, consectetur adipiscing elit. Donec faucibus consequat dui sit amet consequat.</p>
    <div class="circ"><svg width="8" height="10" viewBox="0 0 8 10"><path d="M2 1l4 4-4 4" fill="none" stroke="#fff" stroke-width="2"/></svg></div>
  </div>
  <div class="feature">
    <svg width="38" height="34" viewBox="0 0 38 34"><path d="M3 32V12l8-5v5l8-5v5l8-5V2h6v30z" fill="none" stroke="#0171A1" stroke-width="2"/><rect x="8" y="18" width="5" height="5" fill="#5fb3d6"/><rect x="16" y="18" width="5" height="5" fill="#5fb3d6"/><rect x="24" y="18" width="5" height="5" fill="#5fb3d6"/><line x1="1" y1="32" x2="37" y2="32" stroke="#0171A1" stroke-width="2"/></svg>
    <h3>Feature 04</h3><hr><p>Lorem ipsum dolor sit amet, consectetur adipiscing elit. Donec faucibus consequat dui sit amet consequat.</p>
    <div class="circ"><svg width="8" height="10" viewBox="0 0 8 10"><path d="M2 1l4 4-4 4" fill="none" stroke="#fff" stroke-width="2"/></svg></div>
  </div>
</div>

<!-- products -->
<div class="abs bg-light" style="top:872px;height:793px"></div>
<h2 class="abs sec-title" style="top:952px">Our Products</h2>

<div class="abs product" style="left:162px;top:1024px"><div class="pic" role="img" aria-label="Servo motor product photo"></div><div class="info"><h3>Product Title</h3><p>Cras ultricies ligula sed magna dictum porta. Curabitur<br>non nulla sit amet nisl tempus convallis quis ac lectus.</p><span class="btn btn-black">View Details</span></div></div>
<div class="abs product" style="left:615px;top:1024px"><div class="pic" role="img" aria-label="Servo motor product photo"></div><div class="info"><h3>Product Title</h3><p>Cras ultricies ligula sed magna dictum porta. Curabitur<br>non nulla sit amet nisl tempus convallis quis ac lectus.</p><span class="btn btn-black">View Details</span></div></div>
<div class="abs product" style="left:162px;top:1221px"><div class="pic" role="img" aria-label="Servo motor product photo"></div><div class="info"><h3>Product Title</h3><p>Cras ultricies ligula sed magna dictum porta. Curabitur<br>non nulla sit amet nisl tempus convallis quis ac lectus.</p><span class="btn btn-black">View Details</span></div></div>
<div class="abs product" style="left:615px;top:1221px"><div class="pic" role="img" aria-label="Servo motor product photo"></div><div class="info"><h3>Product Title</h3><p>Cras ultricies ligula sed magna dictum porta. Curabitur<br>non nulla sit amet nisl tempus convallis quis ac lectus.</p><span class="btn btn-black">View Details</span></div></div>
<div class="abs product" style="left:162px;top:1417px"><div class="pic" role="img" aria-label="Servo motor product photo"></div><div class="info"><h3>Product Title</h3><p>Cras ultricies ligula sed magna dictum porta. Curabitur<br>non nulla sit amet nisl tempus convallis quis ac lectus.</p><span class="btn btn-black">View Details</span></div></div>
<div class="abs product" style="left:615px;top:1417px"><div class="pic" role="img" aria-label="Servo motor product photo"></div><div class="info"><h3>Product Title</h3><p>Cras ultricies ligula sed magna dictum porta. Curabitur<br>non nulla sit amet nisl tempus convallis quis ac lectus.</p><span class="btn btn-black">View Details</span></div></div>

<!-- measure up -->
<h2 class="abs sec-title" style="top:1743px">Measure Up</h2>

<div class="abs measure" style="top:1811px;height:273px">
  <div class="abs ring" role="img" aria-label="Angled planetary gearbox photo"></div>
  <h3 class="abs">Title Here</h3>
  <p class="abs">Lorem ipsum dolor sit amet, consectetur adipiscing elit. Proin eu felis felis. Donec at pellentesque enim. Quisque vehicula nunc felis, ut porttitor ipsum convallis quis. Praesent vel facilisis ex. Mauris cursus sit amet augue ut porttitor. Integer pellentesque risus vitae pellentesque fringilla. In eu imperdiet enim. Integer dolor ligula, malesuada a dolor non, congue eleifend tortor.</p>
  <div class="abs acts"><span class="btn btn-blue">Free Ticket</span><span class="btn btn-black" style="text-transform:none">View Details</span></div>
</div>
<div class="abs measure" style="top:2101px;height:271px">
  <div class="abs ring" role="img" aria-label="Angled planetary gearbox photo"></div>
  <h3 class="abs">Title Here</h3>
  <p class="abs">Lorem ipsum dolor sit amet, consectetur adipiscing elit. Proin eu felis felis. Donec at pellentesque enim. Quisque vehicula nunc felis, ut porttitor ipsum convallis quis. Praesent vel facilisis ex. Mauris cursus sit amet augue ut porttitor. Integer pellentesque risus vitae pellentesque fringilla. In eu imperdiet enim. Integer dolor ligula, malesuada a dolor non, congue eleifend tortor.</p>
  <div class="abs acts"><span class="btn btn-blue">Free Ticket</span><span class="btn btn-black" style="text-transform:none">View Details</span></div>
</div>
<div class="abs measure" style="top:2395px;height:271px">
  <div class="abs ring" role="img" aria-label="Angled planetary gearbox photo"></div>
  <h3 class="abs">Title Here</h3>
  <p class="abs">Lorem ipsum dolor sit amet, consectetur adipiscing elit. Proin eu felis felis. Donec at pellentesque enim. Quisque vehicula nunc felis, ut porttitor ipsum convallis quis. Praesent vel facilisis ex. Mauris cursus sit amet augue ut porttitor. Integer pellentesque risus vitae pellentesque fringilla. In eu imperdiet enim. Integer dolor ligula, malesuada a dolor non, congue eleifend tortor.</p>
  <div class="abs acts"><span class="btn btn-blue">Free Ticket</span><span class="btn btn-black" style="text-transform:none">View Details</span></div>
</div>

<!-- about -->
<div class="abs bg-light" style="top:2767px;height:513px"></div>
<h2 class="abs about-title">About Us</h2>
<div class="abs about-bar"></div>
<div class="abs about-text">
  <div class="lead">Lorem ipsum dolor sit amet, consectetur adipiscing elit. Proin eu felis felis. Donec at pellentesque enim.</div>
  <p>Lorem Ipsum is simply dummy text of the printing and typesetting industry. Lorem Ipsum has been the industry's standard dummy text ever since the 1500s Lorem Ipsum is simply dummy text of the printing and typesetting industry.</p>
  <p>Lorem ipsum dolor sit amet, consectetur adipiscing elit. Proin eu felis felis.</p>
  <div style="margin-top:18px"><span class="btn btn-black" style="text-transform:none;padding:11px 30px">Read More</span></div>
</div>
<div class="abs photo-big" role="img" aria-label="Office desk with coffee mug and milk bottle"></div>
<div class="abs photo-small" role="img" aria-label="Compact geared motor photo"></div>

<!-- downloads -->
<div class="abs dl-photo" role="img" aria-label="Close-up of an engine with belts and pulleys"></div>
<div class="abs dl-text">
  <h2>Downloads</h2>
  <p>Lorem ipsum dolor sit amet, consectetur adipiscing elit. Proin eu felis felis. Donec at pellentesque enim. Quisque vehicula nunc felis, ut porttitor ipsum convallis quis. Praesent vel facilisis ex. Mauris cursus sit amet augue ut porttitor. Integer pellentesque risus vitae pellentesque fringilla. In eu imperdiet enim. Integer dolor ligula, malesuada a dolor non, congue eleifend tortor. Sed feugiat odio nec diam vulputate malesuada.</p>
  <p>Lorem ipsum dolor sit amet, consectetur adipiscing elit. Proin eu felis felis. Donec at pellentesque enim. Quisque vehicula nunc felis, ut porttitor ipsum convallis quis. Praesent vel facilisis ex. Mauris cursus sit amet augue ut porttitor. Integer pellentesque risus vitae pellentesque fringilla. In eu imperdiet enim. Integer dolor ligula, malesuada a dolor non, congue eleifend tortor. Sed feugiat odio nec diam vulputate malesuada.</p>
</div>
<div class="abs dl-btn">DOWNLOAD <svg width="9" height="10" viewBox="0 0 9 10"><path d="M4.5 0v6M1.5 3.5l3 3 3-3M0 9h9" fill="none" stroke="#111" stroke-width="1.6"/></svg></div>

<!-- contact -->
<div class="abs contact">
  <h2>Contact Us</h2>
  <div class="abs input" style="left:356px;top:121px;width:240px">Phone</div>
  <div class="abs input" style="left:604px;top:121px;width:240px">Email Address</div>
  <div class="abs submit">SUBMIT</div>
</div>

<!-- info row -->
<div class="abs info-item" style="left:162px">
  <svg width="54" height="54" viewBox="0 0 54 54"><path d="M27 4a12 12 0 0 0-12 12c0 9 12 22 12 22s12-13 12-22A12 12 0 0 0 27 4z" fill="none" stroke="#0171A1" stroke-width="2"/><circle cx="27" cy="16" r="4.5" fill="none" stroke="#0171A1" stroke-width="2"/><path d="M14 34l-11 16h48L40 34" fill="none" stroke="#0171A1" stroke-width="2"/></svg>
  <div><b>Address</b><span>Lorem ipsum dolor sit<br>amet.</span></div>
</div>
<div class="abs info-item" style="left:402px">
  <svg width="54" height="54" viewBox="0 0 54 54"><path d="M3 18c0-6 48-6 48 0v5h-11v-5H14v5H3z" fill="none" stroke="#0171A1" stroke-width="2"/><path d="M10 26l-4 24h42l-4-24z" fill="none" stroke="#0171A1" stroke-width="2"/><text x="27" y="44" text-anchor="middle" font-family="Open Sans, sans-serif" font-weight="700" font-size="13" fill="#0171A1">24</text></svg>
  <div><b>Contact Info</b><span>+49 (0) 987654321<br>+49 (0) 987654321</span></div>
</div>
<div class="abs info-item" style="left:634px">
  <svg width="54" height="54" viewBox="0 0 54 54"><rect x="3" y="20" width="48" height="30" fill="none" stroke="#0171A1" stroke-width="2"/><path d="M3 20l24 18 24-18M3 50l18-16M51 50L33 34" fill="none" stroke="#0171A1" stroke-width="2"/><rect x="13" y="4" width="28" height="24" fill="#fff" stroke="#0171A1" stroke-width="2"/><line x1="18" y1="11" x2="36" y2="11" stroke="#0171A1" stroke-width="2"/><line x1="18" y1="17" x2="36" y2="17" stroke="#0171A1" stroke-width="2"/></svg>
  <div><b>Email Address</b><span>info@kvm-motors.example<br>info@kvm-motors.example</span></div>
</div>
<div class="abs touch">Get in Touch</div>
<div class="abs divider"></div>

<!-- footer -->
<div class="abs f-col" style="left:162px;top:4232px"><h5>Our Solutions</h5><ul><li>Lorem ipsum is dolor</li><li>Lorem ipsum is dolor</li><li>Lorem ipsum is dolor</li><li>Lorem ipsum is dolor</li><li>Lorem ipsum is dolor</li></ul></div>
<div class="abs f-col" style="left:389px;top:4232px"><h5>Company</h5><ul><li>Home</li><li>Company News</li><li>Case Study</li><li>Awards</li><li>Contact Us</li></ul></div>
<div class="abs f-col" style="left:537px;top:4261px"><ul><li>About Us</li><li>Products</li><li>Faq's</li><li>Services</li><li>Our Team</li></ul></div>
<div class="abs f-col" style="left:690px;top:4232px"><h5>Subscribe Our Newsletter</h5><ul><li>Weekly Breaking News Analysis And Cutting Edge</li><li>Advices On Job Searching</li></ul></div>
<div class="abs news-input">Email Address</div>
<div class="abs news-btn">SUBSCRIBE</div>
<div class="abs socials"><i></i><i></i><i></i><i></i></div>

<div class="abs bottom">
  <span class="abs" style="left:162px;top:19px">Copyright © 2020. All Rights Reserved.</span>
  <span class="abs" style="left:880px;top:19px;word-spacing:14px">Home About FAQs Contact</span>
</div>

</body>
</html>
```